Specialised investor in e-mobility and energy wants business card design

We need a business card design that fits our existing corporate design. <The look and feel must be 'sharp'/'clean', dynamic, communicate momentum, professionalism etc (as one would imagine from a firm in the financial sector). We like the idea of a reverse-side of the card that includes the logo, and the name and contact details on the other. We expect the deliverable to be whatever format might be required to be able to get cards printed directly by a service such as kelmo press. Our website is www.zub.capital

```html
<!DOCTYPE html>
<html lang="en">
<head>
<meta charset="utf-8">
<title>Zub Capital – Business Card</title>
<link rel="stylesheet" href="https://fonts.googleapis.com/css2?family=Raleway:wght@400;500;800&display=swap">
<style>
  :root {
    --bg: #e9ebe7;
    --paper: #ffffff;
    --green-dark: #2f4f22;
    --green-light: #7cb342;
    --green-back: #33532a;
    --green-emboss: #3e6233;
    --ink: #3a3a3a;
  }
  * { box-sizing: border-box; margin: 0; padding: 0; }
  html, body { width: 1200px; height: 856px; overflow: hidden; }
  body {
    background: var(--bg);
    font-family: "Raleway", sans-serif;
    display: flex;
    align-items: center;
    justify-content: center;
    gap: 44px;
  }
  .card {
    position: relative;
    width: 525px;
    height: 300px;
    overflow: hidden;
    box-shadow: 0 6px 18px rgba(0,0,0,.18);
  }
  .card-front { background: var(--paper); }
  .card-back { background: var(--green-back); display: flex; align-items: center; justify-content: center; }

  .brand-name {
    position: absolute;
    top: 34px;
    left: 118px;
    font-weight: 500;
    font-size: 66px;
    line-height: 1;
    color: var(--green-dark);
    letter-spacing: -1px;
  }
  .accent-tab {
    position: absolute;
    left: 0;
    top: 150px;
    width: 30px;
    height: 10px;
    background: var(--green-light);
  }
  .person {
    position: absolute;
    left: 42px;
    top: 146px;
  }
  .person-name {
    font-weight: 800;
    font-size: 16px;
    color: var(--green-light);
    letter-spacing: .3px;
  }
  .person-role {
    font-size: 12px;
    color: var(--ink);
    margin-top: 2px;
  }
  .contacts {
    position: absolute;
    left: 42px;
    top: 198px;
    list-style: none;
    font-size: 12px;
    color: var(--ink);
  }
  .contacts li { display: flex; align-items: center; gap: 7px; height: 18px; }
  .contacts svg { width: 11px; height: 11px; flex: none; }
  .divider {
    position: absolute;
    left: 200px;
    top: 180px;
    width: 300px;
    height: 2px;
    background: var(--green-light);
  }
  .address {
    position: absolute;
    right: 26px;
    top: 198px;
    text-align: right;
    font-size: 13px;
    line-height: 1.45;
    color: var(--ink);
  }
  .edge-band {
    position: absolute;
    left: 0;
    bottom: 0;
    width: 100%;
    height: 12px;
    background: var(--green-light);
  }
  .back-name {
    font-weight: 500;
    font-size: 70px;
    color: var(--green-emboss);
    letter-spacing: -1px;
  }
</style>
</head>
<body>
  <section class="card card-front" aria-label="Business card front">
    <div class="brand-name">Zub Capital</div>
    <div class="accent-tab"></div>
    <div class="person">
      <p class="person-name">MARCUS ELLWOOD</p>
      <p class="person-role">Managing Director</p>
    </div>
    <div class="divider"></div>
    <ul class="contacts">
      <li>
        <svg viewBox="0 0 12 12"><rect width="12" height="12" rx="2" fill="var(--green-light)"/><path d="M3.5 2.8l1.4 0 .6 1.8-.9.7a5 5 0 0 0 2.1 2.1l.7-.9 1.8.6v1.4c0 .4-.4.7-.8.7A6 6 0 0 1 2.8 3.6c0-.4.3-.8.7-.8z" fill="#fff"/></svg>
        +41 79555 0148
      </li>
      <li>
        <svg viewBox="0 0 12 12"><rect width="12" height="12" rx="2" fill="var(--green-light)"/><rect x="2.5" y="3.5" width="7" height="5" fill="#fff"/><path d="M2.5 3.5l3.5 2.8 3.5-2.8" fill="none" stroke="var(--green-light)" stroke-width=".8"/></svg>
        marcus@zub.capital
      </li>
      <li>
        <svg viewBox="0 0 12 12"><circle cx="6" cy="6" r="6" fill="var(--green-light)"/><circle cx="6" cy="6" r="3.4" fill="none" stroke="#fff" stroke-width=".9"/><path d="M2.6 6h6.8M6 2.6v6.8" stroke="#fff" stroke-width=".8"/></svg>
        www.zub.capital
      </li>
    </ul>
    <address class="address">Zub Capital S.A.<br>Geneva, Switzerland</address>
    <div class="edge-band"></div>
  </section>

  <section class="card card-back" aria-label="Business card back">
    <div class="back-name">Zub Capital</div>
  </section>
</body>
</html>
```